Personal Trainer website design

We are working with a personal trainer to design a website. They offer their primary services: Diet Coaching, In-Person Coaching (workouts), and Remote Coaching.
Some sites we like: https://www.mirabelthorne.com, https://kavialune.com/en-us, https://corvexfit.co.uk
Thank you for taking the time to consider designing a website for us. We are web developers based in Stockton, CA USA. Most of our projects go through the same process. Understanding this process may help you win a project with us. We custom-code all of our websites in-house. We don’t have any requirements as to what tools you use for your design, but ask that you follow these guidelines.
IMAGES:
We ask that if you use any images, or icons in the design, have a link to the asset, so we can purchase the image/icon. Most of the designs we submit do not have the customer’s images on them unless they have some great images. Be creative; show us the feeling that you are trying to portray with your image choices. Use any royalty-free site you choose. We subscribe to Quillon and mostly use their images, but are ok to purchase images outside of Quillon.
FONTS:
We ask that you identify the fonts you’re using in the design. This can be done in a message if you want. We typically use Brivane Fonts and Quillon Fonts.
CONTENT:
We're always open to different content and ideas. Often, we submit designs with stock images so that the client can see our vision. We typically go back and take pictures after the website launch to use their images with our vision. Lorem Ipsum is fine for paragraphs, but we ask that you make the Headers with correct English. We want to be able to show the vision and identify the sections of the website.
INSPIRATION:
We try and add a couple of links in the brief of some websites that we like to help you get started in your design.
REVISIONS:
We do not often ask for revisions of the designs unless we see something in the design that may not appeal to the client. If there are slight changes that we want to make, we simply do that in the development process.
FEEDBACK:
We rarely give feedback on designs during the design process. We are working on many website projects and do not have the time to give feedback. We usually respond if your request is well thought out and asks specific questions, but a note asking “feedback, please” usually goes unanswered.
1 page

```html
<!DOCTYPE html>
<html lang="en">
<head>
<meta charset="utf-8">
<title>Novafit — Personal Trainer</title>
<link rel="stylesheet" href="https://fonts.googleapis.com/css2?family=Bebas+Neue&family=DM+Serif+Display&family=Inter:wght@400;500;600&display=swap">
<style>
:root{
  --olive:#8a9a17;
  --olive-dark:#6f7c10;
  --board:#e8ecd6;
  --board-mark:#ccd1b4;
  --ink:#1d1d1b;
  --muted:#6b6b66;
  --paper:#ffffff;
  --stone:#d9d5cf;
  --card:#f1f0ee;
  --serif:"DM Serif Display", Georgia, serif;
  --sans:"Inter", Arial, sans-serif;
  --cond:"Bebas Neue", Impact, sans-serif;
}
*{box-sizing:border-box;margin:0;padding:0}
html,body{width:1200px;height:1200px;overflow:hidden;background:var(--board)}
.board{position:absolute;left:0;top:0;width:1932px;height:1932px;transform:scale(.62112);transform-origin:0 0;background:var(--board);font-family:var(--sans);color:var(--ink)}
.board-mark{position:absolute;left:300px;top:1460px;transform:rotate(-90deg);transform-origin:0 0;font-family:var(--cond);font-size:280px;letter-spacing:30px;color:var(--board-mark);line-height:1;white-space:nowrap}
.page{position:absolute;left:660px;top:111px;width:612px;height:1709px;background:var(--paper);overflow:hidden;box-shadow:0 10px 30px rgba(60,70,20,.12)}
.abs{position:absolute}
.photo{position:absolute}
.btn{position:absolute;height:16px;border-radius:8px;background:var(--olive);color:#fff;font-size:4.5px;font-weight:500;display:flex;align-items:center;justify-content:center;letter-spacing:.2px}
.btn.ghost{background:#dedad5;color:#555}
.eyebrow{position:absolute;font-size:6.5px;color:#333;white-space:nowrap}
.title{position:absolute;font-family:var(--serif);font-size:13px;color:var(--ink);white-space:nowrap}
.title em{font-style:normal;color:var(--olive)}
.copy{position:absolute;font-size:4.6px;line-height:7.7px;color:#333}
/* hero */
.hero{left:0;top:0;width:612px;height:288px}
.logo-tab{left:68px;top:0;width:154px;height:73px;background:rgba(215,213,208,.9);border-radius:0 0 12px 12px;display:flex;align-items:center;justify-content:center;gap:5px}
.wordmark{font-family:var(--cond);font-size:30px;color:#2b2b2b;letter-spacing:1px;line-height:1}
.wordmark-dot{width:14px;height:14px;border-radius:50%;background:var(--olive)}
.nav{left:308px;top:41px;display:flex;gap:6.5px;font-size:4.6px;color:#fff}
.social{top:18px;display:flex;gap:4px;left:453px}
.social i{display:block;width:11px;height:11px;border-radius:50%;background:var(--olive)}
.members{left:473px;top:36px;width:42px;height:15px;border-radius:8px;background:var(--olive);color:#fff;font-size:4.6px;display:flex;align-items:center;justify-content:center}
.search{left:517px;top:38px;width:11px;height:11px;border-radius:50%;background:var(--olive)}
.hero-sub{left:0;width:612px;top:109px;text-align:center;font-size:6px;color:#fff}
.hero-title{left:0;width:612px;top:123px;text-align:center;font-family:var(--serif);font-size:20px;line-height:20px;color:#fff}
.hero-author{left:0;width:612px;top:168px;text-align:center;font-size:6px;color:#fff}
.hero-copy{left:191px;width:230px;top:185px;text-align:center;font-size:4.3px;line-height:7.7px;color:#fff}
/* frames */
.frame{position:absolute;border:1.5px solid var(--olive);border-radius:6px}
.check{display:flex;align-items:center;gap:5px;font-size:4.6px;color:#333;height:11px}
.check svg{width:6px;height:6px}
/* services */
.svc{position:absolute;width:144px;height:144px;border-radius:5px;overflow:hidden}
.svc .photo{inset:0}
.svc h3{position:absolute;left:10px;top:37px;font-family:var(--serif);font-weight:400;font-size:9px;color:#fff}
.svc .rule{position:absolute;left:10px;top:52px;width:14px;height:1px;background:#fff}
.svc p{position:absolute;left:10px;top:61px;width:126px;font-size:4.2px;line-height:7.7px;color:#fff}
.svc .more{position:absolute;left:10px;top:91px;width:45px;height:9px;border-radius:5px;background:#fff;color:#333;font-size:4.2px;display:flex;align-items:center;justify-content:center}
/* press */
.press{left:158px;top:1179px;width:334px;height:56px;background:#dcd9d4;border-radius:4px;display:flex;align-items:center;justify-content:space-around;padding:0 6px}
.press span{font-family:var(--serif);font-size:18px;color:#555}
/* subscribe */
.subscribe{left:81px;top:1270px;width:449px;height:75px;background:#dcd9d4;border-radius:5px}
.field{left:232px;top:24px;width:206px;height:24px;border-radius:12px;background:#fff;font-size:4.6px;color:#555;display:flex;align-items:center;padding-left:10px}
.field-btn{left:380px;top:24px;width:58px;height:24px;border-radius:12px;background:var(--olive);color:#fff;font-size:4.6px;display:flex;align-items:center;justify-content:center}
/* testimonials */
.stars{color:var(--olive);font-size:8px;letter-spacing:1.5px}
.review{position:absolute;top:1377px;width:144px;height:169px;background:#efeeec;border-radius:4px;text-align:center}
.review .avatar{position:absolute;left:42px;top:17px;width:60px;height:60px;border-radius:50%}
.review .name{position:absolute;left:0;right:0;top:84px;font-size:7px;color:var(--olive)}
.review .role{position:absolute;left:0;right:0;top:94px;font-size:4px;color:#666}
.review .stars{position:absolute;left:0;right:0;top:100px;font-size:6px}
.review p{position:absolute;left:8px;right:8px;top:116px;font-size:4.5px;line-height:7.6px;color:#666}
/* footer */
.footer{left:0;top:1578px;width:612px;height:131px;background:var(--stone)}
.foot-h{font-size:9px;color:#333;letter-spacing:.3px}
.foot-s{font-size:5px;color:#444;white-space:nowrap}
.pay{display:flex;gap:3px}
.pay i{display:block;width:14px;height:8px;border-radius:1.5px;background:#fff;border:.5px solid #bbb}
.social-dark{display:block;width:11px;height:11px;border-radius:50%;background:#222}
</style>
</head>
<body>
<div class="board">
  <div class="board-mark">NOVAFIT</div>

  <main class="page">
    <section class="abs hero">
      <div class="photo" style="inset:0;background:linear-gradient(180deg,#bdbbb6 0%,#a9a69f 50%,#7a6656 78%,#574233 100%)" role="img" aria-label="Woman holding a plank on a mat in a bright gym studio"></div>
      <div class="abs logo-tab"><span class="wordmark">NOVAFIT</span><span class="wordmark-dot"></span></div>
      <div class="abs social"><i></i><i></i><i></i><i></i><i></i></div>
      <nav class="abs nav"><span>ABOUT</span><span>SERVICES</span><span>THE JOURNAL</span><span>BLOG</span><span>SHOP</span><span>CONTACT</span></nav>
      <div class="abs members">MEMBERS</div>
      <div class="abs search"></div>
      <p class="abs hero-sub">Your personal workout and diet trainer</p>
      <h1 class="abs hero-title" style="font-weight:400">A healthy outside starts from<br>the inside.</h1>
      <p class="abs hero-author">– Elliot Marsh</p>
      <p class="abs hero-copy">Lorem ipsum dolor sit amet, consectetur adipiscing elit. Vestibulum vel fringilla mi. Integer eu sagittis quam, sit amet volutpat odio. Sed et tincidunt nisi. Integer eget felis quis nulla tincidunt commodo. Sed at tincidunt eros.</p>
      <div class="btn" style="left:282px;top:224px;width:48px">GET STARTED</div>
    </section>

    <div class="frame" style="left:100px;top:332px;width:60px;height:60px;border-right:none;border-bottom:none"></div>
    <div class="photo" style="left:137px;top:320px;width:163px;height:198px;border-radius:4px;background:linear-gradient(160deg,#d9d9d9,#9a9a9a 55%,#4a4a4a)" role="img" aria-label="Trainer reviewing a plan with a client in the gym"></div>
    <div class="photo" style="left:80px;top:360px;width:80px;height:139px;border-radius:4px;background:linear-gradient(160deg,#e6e6e6,#8d8d8d 60%,#3c3c3c);border:1px solid #fff" role="img" aria-label="Trainer and client reading a clipboard"></div>
    <p class="eyebrow" style="left:348px;top:358px">Our Mission, Vission, Passion and History</p>
    <h2 class="title" style="left:348px;top:374px;font-weight:400">About <em>Novafit</em></h2>
    <p class="copy" style="left:348px;top:397px;width:184px">Curabitur tincidunt velit quam, eu condimentum ligula bibendum ac. Duis volutpat mauris eu lacinia lobortis. Nulla facilisi. In accumsan sed massa sit amet pellentesque. Mauris tristique, nunc pharetra vestibulum tempus, ex sem molestie neque, ac varius risus lacus sit amet purus. Cras <span style="color:var(--olive)">laoreet</span> dignissim felis, ac congue augue. Donec blandit sem quis tortor hendrerit mattis. Mauris vitae ultricies libero. Curabitur suscipit dignissim augue, eleifend iaculis quam pellentesque eu. Suspendisse et eros fermentum, rhoncus nulla eu, pharetra sem.</p>
    <div class="btn" style="left:348px;top:463px;width:50px">GET STARTED</div>

    <p class="eyebrow" style="left:81px;top:579px">Our Facilities, Uniqueness And Features</p>
    <h2 class="title" style="left:81px;top:596px;font-weight:400">Why choose <em>Novafit</em></h2>
    <p class="copy" style="left:81px;top:617px;width:172px">Curabitur tincidunt velit quam, eu condimentum ligula bibendum ac. Duis volutpat mauris eu lacinia lobortis.</p>
    <ul class="abs" style="left:81px;top:639px;list-style:none">
      <li class="check"><svg viewBox="0 0 10 10"><circle cx="5" cy="5" r="5" fill="#8a9a17"/><path d="M2.6 5.2l1.6 1.6 3.2-3.4" stroke="#fff" stroke-width="1.2" fill="none"/></svg>Lorem ipsum dolor sit amet</li>
      <li class="check"><svg viewBox="0 0 10 10"><circle cx="5" cy="5" r="5" fill="#8a9a17"/><path d="M2.6 5.2l1.6 1.6 3.2-3.4" stroke="#fff" stroke-width="1.2" fill="none"/></svg>Consectetur adipiscing elit</li>
      <li class="check"><svg viewBox="0 0 10 10"><circle cx="5" cy="5" r="5" fill="#8a9a17"/><path d="M2.6 5.2l1.6 1.6 3.2-3.4" stroke="#fff" stroke-width="1.2" fill="none"/></svg>Sed do eiusmod tempor incididunt</li>
      <li class="check"><svg viewBox="0 0 10 10"><circle cx="5" cy="5" r="5" fill="#8a9a17"/><path d="M2.6 5.2l1.6 1.6 3.2-3.4" stroke="#fff" stroke-width="1.2" fill="none"/></svg>Ut labore et dolore magna aliqua.</li>
      <li class="check"><svg viewBox="0 0 10 10"><circle cx="5" cy="5" r="5" fill="#8a9a17"/><path d="M2.6 5.2l1.6 1.6 3.2-3.4" stroke="#fff" stroke-width="1.2" fill="none"/></svg>Quis ipsum suspendisse ultrices gravida.</li>
    </ul>
    <div class="btn" style="left:81px;top:703px;width:50px">GET STARTED</div>
    <div class="btn ghost" style="left:137px;top:703px;width:49px">BOOK NOW</div>
    <div class="frame" style="left:329px;top:563px;width:60px;height:60px;border-right:none;border-bottom:none"></div>
    <div class="photo" style="left:367px;top:551px;width:163px;height:197px;border-radius:4px;background:linear-gradient(160deg,#ececec,#b9b9b9 55%,#4d4d4d)" role="img" aria-label="Instructor guiding a woman through a stretch on the studio floor"></div>
    <div class="photo" style="left:310px;top:590px;width:104px;height:139px;border-radius:4px;background:linear-gradient(160deg,#e3e3e3,#9a9a9a 55%,#3d3d3d);border:1px solid #fff" role="img" aria-label="Trainer and client checking progress on a tablet"></div>

    <p class="eyebrow" style="left:81px;top:781px">Make A New Start With The New You</p>
    <h2 class="abs" style="left:81px;top:798px;font-family:var(--cond);font-weight:400;font-size:14px;color:var(--ink)">SERVICES FROM <span style="color:var(--olive)">NOVAFIT</span></h2>
    <p class="copy" style="left:81px;top:820px;width:220px">Curabitur tincidunt velit quam, eu condimentum ligula bibendum ac. Duis volutpat mauris eu lacinia lobortis. Nulla facilisi. In accumsan sed massa sit amet pellentesque.</p>

    <article class="svc" style="left:81px;top:846px"><div class="photo" style="background:linear-gradient(160deg,#8d1f2e,#b4344a 60%,#6d1a25)" role="img" aria-label="Athlete stretching on a red studio floor"></div><h3>Studio Classes</h3><div class="rule"></div><p>Curabitur tincidunt velit quam, eu condimentum ligula bibendum ac. Duis volutpat mauris eu lacinia lobortis. Nulla facilisi. In accumsan sed massa</p><div class="more">Know More →</div></article>
    <article class="svc" style="left:234px;top:846px"><div class="photo" style="background:linear-gradient(160deg,#c9b8a8,#9c8a78 55%,#6b5b4e)" role="img" aria-label="Instructor streaming a live class from a phone tripod"></div><h3>Live Classes</h3><div class="rule"></div><p>Curabitur tincidunt velit quam, eu condimentum ligula bibendum ac. Duis volutpat mauris eu lacinia lobortis. Nulla facilisi. In accumsan sed massa</p><div class="more">Know More →</div></article>
    <article class="svc" style="left:387px;top:846px"><div class="photo" style="background:linear-gradient(160deg,#a69c92,#6c635b 55%,#3a3531)" role="img" aria-label="Trainer coaching a client with medicine balls"></div><h3>Personal Training</h3><div class="rule"></div><p>Curabitur tincidunt velit quam, eu condimentum ligula bibendum ac. Duis volutpat mauris eu lacinia lobortis. Nulla facilisi. In accumsan sed massa</p><div class="more">Know More →</div></article>
    <article class="svc" style="left:81px;top:1002px"><div class="photo" style="background:linear-gradient(160deg,#7d8083,#5d6b45 55%,#4a4d50)" role="img" aria-label="Fresh vegetables, fruit and a measuring tape"></div><h3>Diet Coaching</h3><div class="rule"></div><p>Curabitur tincidunt velit quam, eu condimentum ligula bibendum ac. Duis volutpat mauris eu lacinia lobortis. Nulla facilisi. In accumsan sed massa</p><div class="more">Know More →</div></article>
    <article class="svc" style="left:234px;top:1002px"><div class="photo" style="background:linear-gradient(180deg,#8aa3b8,#3f5e78 50%,#5b4c40)" role="img" aria-label="Woman doing lunges on a seaside boardwalk"></div><h3>In-Person Workouts</h3><div class="rule"></div><p>Curabitur tincidunt velit quam, eu condimentum ligula bibendum ac. Duis volutpat mauris eu lacinia lobortis. Nulla facilisi. In accumsan sed massa</p><div class="more">Know More →</div></article>
    <article class="svc" style="left:387px;top:1002px"><div class="photo" style="background:linear-gradient(160deg,#5a4a3c,#2f3a30 55%,#3d4a52)" role="img" aria-label="Man following a remote workout on a laptop at home"></div><h3>Remote Coaching</h3><div class="rule"></div><p>Curabitur tincidunt velit quam, eu condimentum ligula bibendum ac. Duis volutpat mauris eu lacinia lobortis. Nulla facilisi. In accumsan sed massa</p><div class="more">Know More →</div></article>

    <p class="abs" style="left:80px;top:1192px;font-family:var(--cond);font-size:13px;line-height:14px;color:var(--ink)"><span style="color:var(--olive)">CHECK</span><br>US ON</p>
    <svg class="abs" style="left:128px;top:1202px" width="20" height="10" viewBox="0 0 20 10"><path d="M19 5H2M6 1L2 5l4 4" stroke="#1d1d1b" stroke-width="1.8" fill="none"/></svg>
    <div class="abs press"><span>LUMIÈRE</span><span>Ledgerly</span><span style="font-size:13px">The Courier</span><span>MAISON</span></div>
    <svg class="abs" style="left:500px;top:1202px" width="20" height="10" viewBox="0 0 20 10"><path d="M1 5h17M14 1l4 4-4 4" stroke="#1d1d1b" stroke-width="1.8" fill="none"/></svg>

    <section class="abs subscribe">
      <p class="eyebrow" style="left:10px;top:22px">Change Your Life With Us</p>
      <h2 class="title" style="left:10px;top:36px;font-size:11.5px;font-weight:400"><em>Get</em> Latest Updates <em>subscribe</em> now</h2>
      <div class="abs field">Enter Your Email Address</div>
      <div class="abs field-btn">Subscribe Now</div>
    </section>

    <p class="eyebrow" style="left:81px;top:1385px">Our Testimonials</p>
    <h2 class="title" style="left:81px;top:1400px;font-size:11px;line-height:12.5px;font-weight:400">Just don't listen to us,<br>check What People<br>think about us</h2>
    <div class="abs stars" style="left:81px;top:1444px">★★★★★</div>
    <p class="abs" style="left:81px;top:1458px;font-family:var(--serif);font-size:10px">Brivane Rating</p>
    <div class="abs stars" style="left:81px;top:1479px">★★★★★</div>
    <p class="abs" style="left:81px;top:1493px;font-family:var(--serif);font-size:10px">ABCD Rating</p>
    <div class="btn" style="left:81px;top:1521px;width:81px">CHECK ALL TESTIMONIALS</div>

    <article class="review" style="left:196px"><div class="avatar" style="background:#d8d6d2;border:1px solid #999" role="img" aria-label="Portrait of Dana Hale"></div><p class="name">Dana Hale</p><p class="role">Marketing Manager, ABCD</p><div class="stars">★★★★★</div><p>Lorem ipsum dolor sit amet, consectetur adipiscing elit, sed do eiusmod tempor incididunt ut labore et dolore magna aliqua. Quis ipsum suspendisse ultrices gravida. Risus commodo viverra maecenas accumsan lacus vel facilisis.</p></article>
    <article class="review" style="left:351px"><div class="avatar" style="background:#5a5552" role="img" aria-label="Portrait of Priya Nolan"></div><p class="name">Priya Nolan</p><p class="role">Ex Model, Reporter</p><div class="stars">★★★★★</div><p>Lorem ipsum dolor sit amet, consectetur adipiscing elit, sed do eiusmod tempor incididunt ut labore et dolore magna aliqua. Quis ipsum suspendisse ultrices gravida. Risus commodo viverra maecenas accumsan lacus vel facilisis.</p></article>
    <article class="review" style="left:506px;opacity:.35"><div class="avatar" style="background:#c9c2bc" role="img" aria-label="Portrait of Marcus Reed"></div><p class="name">Marcus Reed</p><p class="role">Motivational Speaker</p><div class="stars">★★★★★</div><p>Lorem ipsum dolor sit amet, consectetur adipiscing elit, sed do eiusmod tempor incididunt ut labore et dolore magna aliqua. Quis ipsum suspendisse ultrices gravida. Risus commodo viverra maecenas accumsan lacus vel facilisis.</p></article>

    <footer class="abs footer">
      <div class="abs" style="left:81px;top:38px;display:flex;align-items:center;gap:4px"><span class="wordmark" style="font-size:26px">NOVAFIT</span><span class="wordmark-dot" style="width:12px;height:12px"></span></div>
      <div class="abs" style="left:81px;top:78px;display:flex;gap:3px"><i class="social-dark"></i><i class="social-dark"></i><i class="social-dark"></i><i class="social-dark"></i><i class="social-dark"></i></div>
      <p class="abs" style="left:81px;top:101px;font-size:4px;color:#333;white-space:nowrap">Copyright © 2023, <span style="color:var(--olive)">Novafit</span> All rights reserved.</p>
      <p class="abs foot-h" style="left:196px;top:39px">QUICK LINKS</p>
      <p class="abs foot-s" style="left:196px;top:55px">ABOUT &nbsp;|&nbsp; SERVICES &nbsp;|&nbsp; THE JOURNAL &nbsp;|&nbsp; BLOG &nbsp;|&nbsp; SHOP &nbsp;|&nbsp; CONTACT</p>
      <p class="abs foot-h" style="left:196px;top:73px">CONNECT WITH US</p>
      <p class="abs foot-s" style="left:196px;top:89px">info@novafit.com &nbsp;|&nbsp; support@novafit.com</p>
      <p class="abs foot-s" style="left:425px;top:35px;line-height:11.5px">Search<br>Privacy Policy<br>Terms of Service<br>Members</p>
      <div class="abs pay" style="left:425px;top:88px"><i></i><i></i><i></i><i></i><i></i><i></i></div>
    </footer>
  </main>
</div>
</body>
</html>
```